SEO Friendly Web Design Needed for Leading Software Company

Founded in 1986, TRBW is the market leader for innovative software solutions for the heavy civil construction industry. Our suite of products, including the bestsellers GroundQuote® and SiteTrack®, are used by more than 40,000 workers every day to improve their proficiency at estimating, job management, resource management, safety and equipment maintenance. TRBW also offers new mobile applications and cloud computing services so companies can work on a wide array of devices including laptops, tablets and smartphones.

In addition to high quality software, TRBW is best known for providing world-class customer service, and for its friendly, employee-ownership culture. We offer a full range of professional support options to help customers maximize their software investment including implementation planning, training and INSTANT 24/7 phone support.

Goals, objectives and target audience

The goal of our new layout and design will be to increase conversions, enhance user experience and enhance our SERP rankings.

Our objectives are as follows:
1. Clean and well laid out home page. White space is OK.
2. CTAs in strategic locations throughout to drive conversions and MQLs
3. SEO rich content with appropriate layout to meet our SEO requirements
4. 2 Master Design Templates – Home & Internal
5. Custom Design elements for individual modules

Target Audience:
- Heavy / Civil Construction Industry
- C Level executives or persons in leadership roles who utilize our software
- MEN in the construction industry.

Requirements
Should not have
• Feminine design - our industry is largely male construction workers.
Don't use script or goofy fonts
Don't change the logo, or put it in an image where it is not easily viewable.

```html
<!DOCTYPE html>
<html lang="en">
<head>
<meta charset="utf-8">
<title>TRBW – Home</title>
<link href="https://fonts.googleapis.com/css2?family=Questrial&family=Arimo:wght@400&family=Source+Sans+3:wght@400&display=swap" rel="stylesheet">
<style>
  :root{
    --ink:#4a5566;
    --text:#666b73;
    --orange:#f7941d;
    --line:#cfd2d6;
    --navy:#1b2640;
    --navy-light:#44566f;
    --foot-text:#c9d0da;
    --foot-line:#8a96a8;
    --yellow:#f6c516;
    --photo-a:#8f8a7e;
    --photo-b:#b7bcc2;
    --photo-c:#8a7a68;
  }
  *{box-sizing:border-box;margin:0;padding:0}
  html,body{width:1200px;height:900px;overflow:hidden;background:#fff}
  body{position:relative;font-family:"Arimo",Arial,sans-serif;color:var(--text)}
  .abs{position:absolute}
  .section-title{font-family:"Questrial",sans-serif;font-size:25px;color:var(--ink);letter-spacing:-.3px;white-space:nowrap}
  .marketing-title{left:102px;top:-16px}
  .award-row{left:101px;width:223px;height:61px;border:1px solid var(--line);display:flex}
  .award{flex:1;display:flex;align-items:center;justify-content:center;font-size:14px}
  .award+.award{border-left:1px solid var(--line)}
  .news{left:388px;width:260px}
  .news-item{margin-bottom:15px;font-size:14px;line-height:16px}
  .news-heading{color:var(--orange);font-size:13.5px}
  .social-feed{left:670px;top:43px;width:411px;height:142px;border:1px solid var(--line);display:flex;align-items:center;justify-content:center;font-size:14px}
  .resources-title{left:102px;top:235px}
  .resource{top:289px;display:flex}
  .resource-photo{width:149px;height:99px}
  .resource-body{margin-left:14px;padding-top:-2px}
  .resource-heading{color:var(--orange);font-size:14px;margin-top:-2px;margin-bottom:12px}
  .resource-body li{list-style:none;font-size:14.5px;line-height:24px;margin-left:1px}
  .cta-text{left:215px;top:465px;font-family:"Questrial",sans-serif;font-size:25px;color:var(--ink);letter-spacing:-.3px}
  .cta-button{left:727px;top:458px;width:190px;height:43px;background:var(--orange);color:#fff;font-family:"Source Sans 3",sans-serif;font-size:25px;display:flex;align-items:center;justify-content:center}
  .site-footer{left:0;top:573px;width:1200px;height:327px;background:radial-gradient(ellipse 520px 330px at 560px 330px,var(--navy-light),var(--navy) 100%);overflow:hidden}
  .foot-heading{font-family:"Source Sans 3",sans-serif;font-size:21px;color:#fff;letter-spacing:.6px;top:15px}
  .foot-list{top:56px;list-style:none}
  .foot-list li{font-size:12.5px;color:var(--foot-text);height:26px;line-height:24px;border-bottom:1px solid var(--foot-line);padding-left:14px;position:relative;letter-spacing:.3px}
  .foot-list li::before{content:"›";position:absolute;left:0;top:-1px;font-size:15px;color:#fff}
  .follow li{list-style:none;display:flex;align-items:center;height:41px;font-size:15px;color:var(--foot-text);letter-spacing:.4px}
  .follow .dot{width:32px;height:32px;border-radius:50%;background:#eef0f3;margin-right:16px}
  .copyright{left:0;width:1116px;text-align:center;top:282px;font-size:12px;color:#9aa6b6}
  .copyright span{color:var(--orange)}
  .quick-ribbon{right:0;bottom:0}
</style>
</head>
<body>
  <h2 class="abs section-title marketing-title">Marketing Message&nbsp; (Awards, PR, News, Social, Testimonials, Jobs)</h2>

  <div class="abs award-row" style="top:43px"><div class="award">Award</div><div class="award">Award</div></div>
  <div class="abs award-row" style="top:123px"><div class="award">Award</div><div class="award">Award</div></div>

  <div class="abs news" style="top:42px">
    <div class="news-item"><div class="news-heading">News Heading</div>- Short summary with link to news</div>
    <div class="news-item"><div class="news-heading">News Heading</div>- Short summary with link to news</div>
    <div class="news-item"><div class="news-heading">News Heading</div>- Short summary with link to news</div>
  </div>

  <div class="abs social-feed">Social Feed: Testimonials / Review FP Chirper Circles</div>

  <h2 class="abs section-title resources-title">Work Smarter - Content Resource Section</h2>

  <div class="abs resource" style="left:102px">
    <div class="resource-photo" role="img" aria-label="Two construction workers in hard hats reviewing a tablet on site" style="background:linear-gradient(135deg,var(--photo-b),var(--photo-a))"></div>
    <div class="resource-body"><div class="resource-heading">Construction Problems</div>
      <ul><li>Link to Content Home</li><li>Link to Content Home</li><li>LInk to Content Home</li></ul></div>
  </div>
  <div class="abs resource" style="left:441px">
    <div class="resource-photo" role="img" aria-label="Yellow excavators in front of a glass office tower" style="background:linear-gradient(180deg,#d4d9df,#c9b25a)"></div>
    <div class="resource-body"><div class="resource-heading">Construction Solutions</div>
      <ul><li>Link to Content Home</li><li>Link to Content Home</li><li>LInk to Content Home</li></ul></div>
  </div>
  <div class="abs resource" style="left:775px">
    <div class="resource-photo" role="img" aria-label="Hands and a hard hat over construction blueprints" style="background:linear-gradient(135deg,#5a6a8a,#c8c3b5 60%,var(--photo-c))"></div>
    <div class="resource-body" style="margin-left:12px"><div class="resource-heading">Case Studies</div>
      <ul><li>Link to Content Home</li><li>Link to Content Home</li><li>LInk to Content Home</li></ul></div>
  </div>

  <p class="abs cta-text">Simple text overview to generate action for CTA</p>
  <a class="abs cta-button">CTA</a>

  <footer class="abs site-footer">
    <h3 class="abs foot-heading" style="left:105px">FOLLOW US</h3>
    <ul class="abs follow" style="left:107px;top:55px">
      <li><span class="dot"></span>Chirper</li>
      <li><span class="dot"></span>WorkLink</li>
      <li><span class="dot"></span>RSS</li>
      <li><span class="dot"></span>CallLine</li>
    </ul>

    <h3 class="abs foot-heading" style="left:298px">SOFTWARE</h3>
    <ul class="abs foot-list" style="left:302px;width:128px;top:55px">
      <li>GroundQuote®</li><li>SiteTrack®</li><li>Safety Application</li><li>The Fleetboard</li>
    </ul>

    <h3 class="abs foot-heading" style="left:499px">SERVICES</h3>
    <ul class="abs foot-list" style="left:501px;width:156px;top:55px">
      <li>Cloud Services</li><li>Custom Programming</li><li>Universities</li><li>Instant Support</li><li>Training &amp; Events</li><li>Training Options</li>
    </ul>

    <h3 class="abs foot-heading" style="left:715px">NEWS</h3>
    <ul class="abs foot-list" style="left:717px;width:156px;top:55px">
      <li>Newsroom</li><li>Newsletter</li><li>Press Kit</li><li>Newsletter subscription</li><li>Training &amp; Events</li><li>Careers at TRBW</li><li>Careers in Construction</li>
    </ul>

    <h3 class="abs foot-heading" style="left:925px">ABOUT US</h3>
    <ul class="abs foot-list" style="left:927px;width:156px;top:55px">
      <li>About Trbw</li><li>TRBW Culture Blog</li><li>Contact/More Info</li><li>The TRBW Story</li><li>Map &amp; Directions</li><li>Stability</li><li>Why Choose</li><li style="border-bottom:none">TRBW</li>
    </ul>

    <p class="abs copyright">Copyright © 2013, <span>TRBW</span>. All Rights Reserved</p>
  </footer>

  <svg class="abs quick-ribbon" width="125" height="125" viewBox="0 0 125 125" aria-label="Get started quick start">
    <polygon points="0,125 125,0 125,52 52,125" fill="var(--yellow)"/>
    <line x1="60" y1="125" x2="125" y2="60" stroke="#fff" stroke-width="1"/>
    <g transform="translate(48,118) rotate(-45)" font-family="Source Sans 3, sans-serif" fill="#fff">
      <text x="0" y="0" font-size="19">GET STARTED</text>
      <text x="42" y="20" font-size="15">QUICK START</text>
    </g>
  </svg>
</body>
</html>
```